A clean crisp business card for a Landscape Construction company. Designed to be easy to read contact/ info and also be appealing/interesting, unlike a traditional business card.

Industry/Entity Type

Landscape Construction

Contact Information for Business Card

Company name : Brambleford Landscape Construction, phone number: (877) 62Vista, website:Bramblefordyards.example, Email, sales@bramblefordyards.example

Requirements
Nice to have
• Luxurious finishes/ details…. Icons or emblems next to contact info
Should not have
• Clipart or general pictures

```html
<!DOCTYPE html>
<html lang="en">
<head>
<meta charset="utf-8">
<title>Brambleford Landscape Construction – Business Card</title>
<link rel="stylesheet" href="https://fonts.googleapis.com/css2?family=Cinzel:wght@700&family=Arimo:wght@400&display=swap">
<style>
  :root {
    --bg: #2b2b2d;
    --brand-blue: #216db8;
    --leaf-green: #9bc93b;
    --card-white: #ffffff;
    --ink: #2a2a2a;
  }
  * { margin: 0; padding: 0; box-sizing: border-box; }
  html, body { width: 1200px; height: 900px; overflow: hidden; }
  body {
    background: var(--bg);
    position: relative;
    font-family: "Arimo", Arial, sans-serif;
  }
  .card {
    position: absolute;
    left: 280px;
    width: 640px;
    height: 366px;
    border-radius: 26px;
    overflow: hidden;
  }
  .card--front { top: 70px; background: var(--brand-blue); }
  .card--back { top: 464px; background: var(--card-white); }

  .wordmark {
    font-family: "Cinzel", "Times New Roman", serif;
    font-weight: 700;
    text-align: center;
    line-height: 1.1;
    display: flex;
    flex-direction: column;
    align-items: center;
  }
  .card--front .wordmark {
    position: absolute;
    inset: 0;
    justify-content: center;
    color: var(--card-white);
  }
  .wordmark__name { font-size: 54px; letter-spacing: 1px; }
  .wordmark__tag { font-size: 19px; letter-spacing: 5px; margin-top: 6px; }

  .back__wave { position: absolute; inset: 0; }

  .holder { position: absolute; left: 100px; top: 20px; }
  .holder__name {
    font-family: "Cinzel", "Times New Roman", serif;
    font-weight: 700;
    font-size: 28px;
    line-height: 1.2;
    color: var(--leaf-green);
    letter-spacing: 1px;
  }
  .holder__title { font-size: 17px; line-height: 1.2; color: var(--card-white); margin-top: 2px; }

  .contact {
    position: absolute;
    left: 42px;
    top: 172px;
    color: var(--ink);
    font-size: 16px;
    line-height: 1.3;
    list-style: none;
  }
  .contact__address { padding-left: 24px; margin-bottom: 4px; }
  .contact__row { display: flex; align-items: center; gap: 8px; }
  .contact__icon { width: 16px; height: 16px; fill: var(--brand-blue); flex: none; }

  .card--back .wordmark {
    position: absolute;
    right: 30px;
    bottom: 22px;
    color: var(--brand-blue);
  }
  .card--back .wordmark__name { font-size: 34px; }
  .card--back .wordmark__tag { font-size: 11px; letter-spacing: 2px; margin-top: 4px; }
</style>
</head>
<body>

<section class="card card--front" aria-label="Card front">
  <div class="wordmark">
    <span class="wordmark__name">Brambleford</span>
    <span class="wordmark__tag">LANDSCAPE CONSTRUCTION</span>
  </div>
</section>

<section class="card card--back" aria-label="Card back">
  <svg class="back__wave" viewBox="0 0 640 366" width="640" height="366" aria-hidden="true">
    <path d="M24,0 C24,80 96,122 255,124 L470,126 C560,128 612,150 640,194" fill="none" stroke="var(--leaf-green)" stroke-width="12"/>
    <path d="M0,0 H640 V176 C606,130 556,112 470,112 L255,110 C90,108 22,70 22,0 Z" fill="var(--brand-blue)"/>
  </svg>

  <div class="holder">
    <div class="holder__name">OWEN HARTLEY</div>
    <div class="holder__title">Founder</div>
  </div>

  <ul class="contact">
    <li class="contact__address">4210 S. Marlow Avenue<br>Country Name, AB 41620</li>
    <li class="contact__row">
      <svg class="contact__icon" viewBox="0 0 24 24" aria-hidden="true"><path d="M6.6 10.8a15 15 0 0 0 6.6 6.6l2.2-2.2a1 1 0 0 1 1-.25 11.4 11.4 0 0 0 3.6.57 1 1 0 0 1 1 1V20a1 1 0 0 1-1 1A17 17 0 0 1 3 4a1 1 0 0 1 1-1h3.5a1 1 0 0 1 1 1c0 1.25.2 2.45.57 3.57a1 1 0 0 1-.25 1z"/></svg>
      (877) 62Vista
    </li>
    <li class="contact__row">
      <svg class="contact__icon" viewBox="0 0 24 24" aria-hidden="true"><path d="M2 5h20v14H2z M2 5l10 8 10-8" /></svg>
      sales@bramblefordyards.example
    </li>
    <li class="contact__row">
      <svg class="contact__icon" viewBox="0 0 24 24" aria-hidden="true"><circle cx="12" cy="12" r="10"/><path d="M2 12h20M12 2c3 3 3 17 0 20M12 2c-3 3-3 17 0 20" fill="none" stroke="#fff" stroke-width="1.4"/></svg>
      bramblefordyards.example
    </li>
  </ul>

  <div class="wordmark">
    <span class="wordmark__name">Brambleford</span>
    <span class="wordmark__tag">LANDSCAPE CONSTRUCTION</span>
  </div>
</section>

</body>
</html>
```